Tevlora website

Web design for small consulting firm
It can be simple, easy to find approach

The primary use is business to business for

a. people wanting to find out a bit more of us after receiving a business card
b. Search words to draw people from search engines to us

Target Market(s)

Senior staff of large companies, in their work capacity
MD / CEO / CFO , directors, etc.

Industry/Entity Type

Business

Colors
ffffff
f79020
faa54b
33a6d7

```html
<!DOCTYPE html>
<html lang="en">
<head>
<meta charset="utf-8">
<title>Tevlora — Consulting</title>
<link href="https://fonts.googleapis.com/css2?family=Roboto:wght@400;500;700&family=Open+Sans:wght@400;600;700&display=swap" rel="stylesheet">
<style>
:root{
  --white:#ffffff;
  --orange:#f79020;
  --orange-soft:#faa54b;
  --blue:#0077bf;
  --blue-light:#33a6d7;
  --title-blue:#1d5fa8;
  --text:#555555;
  --dark:#1f1f1f;
  --footer:#262626;
  --footer-base:#161616;
  --footer-text:#8a8a8a;
  --red:#d8262b;
  --line:#d6d6d6;
}
*{margin:0;padding:0;box-sizing:border-box}
html,body{width:1200px;height:2416px;overflow:hidden;background:var(--white)}
body{position:relative;font-family:"Roboto",Arial,sans-serif;color:var(--text)}
.abs{position:absolute}

/* header */
.top-rule{left:0;top:0;width:1200px;height:4px;background:var(--blue)}
.site-header{left:0;top:0;width:1200px;height:84px;border-bottom:1px solid #e8e8e8}
.brand{left:200px;top:22px;display:flex;align-items:center;gap:10px;font-size:34px;font-weight:700;color:var(--blue)}
.brand-dot{width:16px;height:16px;border-radius:50%;background:var(--orange)}
.nav{left:606px;top:0;height:84px;display:flex;gap:4px;font-size:10.5px}
.nav a{display:block;height:84px;line-height:90px;padding:0 13px;color:var(--orange);text-decoration:none}
.nav a.active{background:var(--blue);color:var(--white)}

/* hero */
.hero{left:0;top:84px;width:1200px;height:472px;background:
  radial-gradient(ellipse 380px 300px at 860px 190px,#f8d25a 0%,#f2b02a 40%,transparent 75%),
  linear-gradient(90deg,#3a1d08 0%,#a8440c 14%,#e3780f 38%,#f6a91c 65%,#f8c13c 100%)}
.hero-caption{left:0;top:511px;width:1200px;height:45px;background:rgba(70,60,55,.72)}
.hero-caption span{position:absolute;left:197px;top:12px;color:var(--white);font-size:18px;letter-spacing:.3px}
.hero-dots{left:952px;top:526px;display:flex;gap:5px}
.hero-dots i{width:12px;height:12px;border-radius:50%;border:2px solid var(--white);background:transparent}
.hero-dots i.on{background:var(--orange)}
.hero-arrow{top:300px}

/* section headings */
.heading{width:1200px;left:0;text-align:center;color:var(--orange);font-size:24px;font-weight:400}

.intro{left:200px;top:612px;width:800px;text-align:center;font-size:10px;line-height:19.2px;color:var(--text)}

/* values */
.values{left:259px;top:794px;width:691px;height:237px;border-top:3px solid var(--line);border-bottom:4px solid var(--orange);display:flex}
.value{flex:1;position:relative;text-align:center}
.value+.value{border-left:3px solid var(--line)}
.value::after{content:"";position:absolute;left:-3px;bottom:-12px;width:3px;height:12px;background:var(--orange)}
.value:first-child::after{display:none}
.value svg{position:absolute;left:50%;top:34px;transform:translateX(-50%)}
.value h3{position:absolute;top:100px;left:0;right:0;font-size:14.5px;font-weight:400;color:var(--orange)}
.value p{position:absolute;top:130px;left:12px;right:12px;font-size:9.8px;line-height:19.5px;color:var(--text)}
.value a{position:absolute;top:192px;left:0;right:0;font-size:9.5px;color:var(--red);text-decoration:none}

/* what we do */
.what{left:0;top:1095px;width:1200px;height:326px;background:var(--blue)}
.what h2{position:absolute;left:200px;top:38px;color:var(--white);font-size:24px;font-weight:400}
.video{position:absolute;left:200px;top:84px;width:349px;height:198px;background:radial-gradient(ellipse 90px 80px at 50% 50%,#ecd9a0 0%,#f6f1e3 55%,#ffffff 100%)}
.video .bar-top{position:absolute;left:0;top:0;width:100%;height:14px;background:#2a2a2a}
.video .bar-bottom{position:absolute;left:0;bottom:0;width:100%;height:16px;background:#1b1b1b}
.what-copy{position:absolute;left:567px;top:98px;width:415px;color:var(--white);font-size:9.8px;font-weight:700;line-height:19.2px}
.what-copy a{color:var(--white);text-decoration:none}

/* articles */
.article{top:1493px;width:252px}
.article .photo{width:252px;height:134px;border:3px solid #ececec;box-shadow:0 0 2px rgba(0,0,0,.35)}
.article h3{margin-top:16px;font-size:18px;font-weight:400;color:var(--title-blue)}
.article p{margin-top:6px;font-size:9.8px;line-height:15.5px;color:var(--text)}
.article a{display:block;margin-top:8px;font-size:9.5px;color:var(--red);text-decoration:none}

.subline{left:0;width:1200px;text-align:center;font-size:11px;font-weight:700;color:#222}

.client{top:1893px;height:34px;display:flex;align-items:center;gap:8px;font-size:28px;font-weight:700;color:#8d8d8d;letter-spacing:-.5px}
.client i{width:16px;height:16px;background:#8d8d8d}

/* request */
.request{left:0;top:2039px;width:1200px;height:105px;background:
  linear-gradient(90deg,#3b3b3d 0%,#8d8a88 20%,#b9b4ad 42%,#6b6966 60%,#a09a95 78%,#4b4849 100%)}
.field{position:absolute;top:35px;height:38px;background:var(--white);border:1px solid #ccc;font-size:9.5px;color:#666;padding:12px 10px}
.field.select::after{content:"";position:absolute;right:14px;top:13px;width:7px;height:7px;border-right:1.5px solid #666;border-bottom:1.5px solid #666;transform:rotate(45deg)}
.submit{position:absolute;left:838px;top:35px;width:146px;height:38px;background:var(--blue);color:var(--white);font-size:11px;text-align:center;line-height:38px}

/* footer */
.footer{left:0;top:2144px;width:1200px;height:200px;background:var(--footer);font-family:"Open Sans",Arial,sans-serif}
.fcol{position:absolute;top:22px}
.fcol h4{font-size:11.5px;font-weight:700;color:var(--white);margin-bottom:12px}
.fcol li{list-style:none;font-size:9.8px;line-height:24px;color:var(--footer-text)}
.office-row{display:flex;gap:14px;font-size:9.8px;line-height:16px;color:#bbbbbb;margin-bottom:16px}
.office-row svg{flex:none;margin-top:2px}
.tweet{font-size:8.8px;line-height:14px;color:var(--footer-text);margin-bottom:14px}
.tweet a{color:var(--blue-light);text-decoration:none}
.tweet small{display:block;font-size:7px;line-height:10px;color:#6a6a6a}
.base{left:0;top:2344px;width:1200px;height:72px;background:var(--footer-base)}
.base p{position:absolute;left:200px;top:30px;font-size:11px;color:var(--white);font-family:"Open Sans",Arial,sans-serif}
.social{position:absolute;top:22px;width:29px;height:29px;border-radius:50%;background:#e9e9e9}
</style>
</head>
<body>

<header class="abs site-header">
  <div class="abs top-rule"></div>
  <div class="abs brand"><span class="brand-dot"></span>Tevlora</div>
  <nav class="abs nav">
    <a class="active" href="#">Home</a>
    <a href="#">About Us</a>
    <a href="#">Services</a>
    <a href="#">Clients</a>
    <a href="#">News</a>
    <a href="#">Contact us</a>
  </nav>
</header>

<section class="abs hero" role="img" aria-label="Golden figures lifting a large light bulb on a warm orange background"></section>
<svg class="abs hero-arrow" style="left:80px" width="20" height="32" viewBox="0 0 20 32"><path d="M16 2 4 16l12 14" fill="none" stroke="#0a78c2" stroke-width="6"/></svg>
<svg class="abs hero-arrow" style="left:1126px" width="20" height="32" viewBox="0 0 20 32"><path d="M4 2l12 14L4 30" fill="none" stroke="#0a78c2" stroke-width="6"/></svg>
<div class="abs hero-caption"><span>NORTHLINE LEADERSHIP FORUM 2014</span></div>
<div class="abs hero-dots"><i class="on"></i><i></i><i></i></div>

<h2 class="abs heading" style="top:576px">Who we are</h2>
<p class="abs intro">Nulla hendrerit diam sit amet purus dignissim bibendum ac eu urna. Praesent convallis lectus in vehicula scelerisque. Mauris fermentum sodales sodales. Etiam tempor pharetra quam at viverraNulla hendrerit diam sit amet purus dignissim bibendum ac eu urna. Praesent convallis lectus in vehicula scelerisque. Mauris fermentum sodales sodales. Etiam tempor pharetra quam at viverra.Nulla hendrerit diam sit amet purus dignissim bibendum ac eu urna. Praesent convallis lectus in vehicula scelerisque. Mauris fermentum sodales sodales. Etiam tempor pharetra quam at viverra.Nulla hendrerit diam sit amet purus dignissim bibendum ac eu urna. Praesent convallis lectus in vehicula scelerisque. Mauris fermentum sodales sodales. Etiam tempor pharetra quam at viverra.Nulla hendrerit diam sit amet purus dignissim bibendum ac eu urna. Praesent convallis lectus in vehicula scelerisque.</p>

<h2 class="abs heading" style="top:738px">Our Values</h2>
<div class="abs values">
  <div class="value">
    <svg width="46" height="34" viewBox="0 0 46 34"><rect x="7" y="3" width="32" height="22" rx="2" fill="none" stroke="#0a78c2" stroke-width="3"/><path d="M1 28h44v3H1z" fill="#0a78c2"/></svg>
    <h3>Event Technology</h3>
    <p>All the tech toys and support that make events flow and impress. All the tech toys and support that</p>
    <a href="#">Read More +</a>
  </div>
  <div class="value">
    <svg width="24" height="34" viewBox="0 0 24 34"><rect x="3" y="2" width="18" height="30" rx="3" fill="none" stroke="#0a78c2" stroke-width="3"/><circle cx="12" cy="27" r="2" fill="#0a78c2"/></svg>
    <h3>Virtual Meetings</h3>
    <p>All the tech toys and support that make events flow and impress. All the tech toys and support that</p>
    <a href="#">Read More +</a>
  </div>
  <div class="value">
    <svg width="44" height="40" viewBox="0 0 44 40"><path d="M6 36 32 10" stroke="#0a78c2" stroke-width="5" stroke-linecap="round"/><path d="M34 2v8M30 6h8M16 6v6M13 9h6M38 18v6M35 21h6" stroke="#0a78c2" stroke-width="2"/></svg>
    <h3>Audio Visual Services</h3>
    <p>All the tech toys and support that make events flow and impress. All the tech toys and support that</p>
    <a href="#">Read More +</a>
  </div>
  <div class="value">
    <svg width="46" height="36" viewBox="0 0 46 36"><ellipse cx="18" cy="14" rx="16" ry="12" fill="#0a78c2"/><path d="M8 23l-4 9 10-6z" fill="#0a78c2"/><ellipse cx="31" cy="21" rx="13" ry="10" fill="#0a78c2" stroke="#fff" stroke-width="2.5"/><path d="M38 29l5 6-10-4z" fill="#0a78c2"/></svg>
    <h3>Custom Event Solutions</h3>
    <p>All the tech toys and support that make events flow and impress. All the tech toys and support that</p>
    <a href="#">Read More +</a>
  </div>
</div>

<section class="abs what">
  <h2>What we do</h2>
  <div class="video" role="img" aria-label="Embedded video still of a golden figure holding a trophy">
    <div class="bar-top"></div>
    <div class="bar-bottom"></div>
  </div>
  <div class="what-copy">
    <p>Lorem ipsum dolor sit amet, consectetur adipisicing elit. Cumque, quos, ratione, optio, blanditiis deserunt saepe iure sunt odit atque eius voluptatum labore excepturi explicabo aliquid sapiente porro voluptas commodi sint?</p>
    <p>Lorem ipsum dolor sit amet, consectetur adipisicing elit. Rerum, quas, quibusdam, impedit duci-mus nisi fugiat veritatis cupiditate commodi</p>
    <p>Lorem ipsum dolor sit amet, consectetur adipisicing elit. Cumque, quos, ratione, optio, blanditiis deserunt saepe iure sunt odit atque eius voluptatum labore excepturi explicabo aliquid sapiente porro voluptas commodi sint?</p>
    <p style="margin-top:6px"><a href="#">Read More +</a></p>
  </div>
</section>

<h2 class="abs heading" style="top:1444px">Articles and publications</h2>
<article class="abs article" style="left:200px">
  <div class="photo" role="img" aria-label="Club night crowd with a performer on stage" style="background:linear-gradient(135deg,#2a1d22,#7a4a4e 45%,#c8a7a0 60%,#3b2a30)"></div>
  <h3>Club</h3>
  <p>Lorem ipsum dolor sit amet, consectetur adipiscing elit. Nulla convallis egestas rhoncus. Donec facilisis fermen-tum sem, ac viverra ante luctus vel. Donec vel mauris quam.</p>
  <a href="#">Read More..</a>
</article>
<article class="abs article" style="left:474px">
  <div class="photo" role="img" aria-label="Dancing crowd at a members event" style="background:linear-gradient(135deg,#3a1e26,#8d5b63 45%,#d9b4b0 58%,#4a2a33)"></div>
  <h3>Membership</h3>
  <p>Lorem ipsum dolor sit amet, consectetur adipiscing elit. Nulla convallis egestas rhoncus. Donec facilisis fermen-tum sem, ac viverra ante luctus vel. Donec vel mauris quam.</p>
  <a href="#">Read More..</a>
</article>
<article class="abs article" style="left:747px">
  <div class="photo" role="img" aria-label="Person in a striped shirt at a training session" style="background:linear-gradient(135deg,#0f3b36,#2f7c68 40%,#cfd8d4 55%,#1d2a2a)"></div>
  <h3>Training</h3>
  <p>Lorem ipsum dolor sit amet, consectetur adipiscing elit. Nulla convallis egestas rhoncus. Donec facilisis fermen-tum sem, ac viverra ante luctus vel. Donec vel mauris quam.</p>
  <a href="#">Read More..</a>
</article>

<h2 class="abs heading" style="top:1813px">Clients</h2>
<p class="abs subline" style="top:1852px">Lorem ipsum dolor sit amet, consectetur adipisicing elit, sed do eiusmod tempor</p>
<div class="abs client" style="left:228px"><i></i>HARWICK</div>
<div class="abs client" style="left:418px">CORVALE</div>
<div class="abs client" style="left:630px">Lumenra</div>
<div class="abs client" style="left:822px">OSTRAND</div>

<h2 class="abs heading" style="top:1968px">Request</h2>
<p class="abs subline" style="top:2006px">Lorem ipsum dolor sit amet, consectetur adipisicing elit, sed do eiusmod tempor</p>

<section class="abs request" role="img" aria-label="Blurred photo of an audience in a conference hall">
  <div class="field" style="left:211px;width:147px">Name</div>
  <div class="field" style="left:366px;width:145px">Email</div>
  <div class="field" style="left:519px;width:146px">Phone</div>
  <div class="field select" style="left:673px;width:147px">Silver</div>
  <div class="submit">Submit</div>
</section>

<footer class="abs footer">
  <div class="fcol" style="left:203px">
    <h4>COMPANY</h4>
    <ul><li>Site Template</li><li>Theme Library</li><li>Blog</li><li>Forum</li><li>Wiki</li></ul>
  </div>
  <div class="fcol" style="left:343px">
    <h4>META</h4>
    <ul><li>Log in</li><li>Entries RSS</li><li>Comments RSS</li><li>Resources</li></ul>
  </div>
  <div class="fcol" style="left:483px;width:260px">
    <h4>HEAD OFFICE</h4>
    <div class="office-row"><svg width="10" height="13" viewBox="0 0 10 13"><path d="M5 0a5 5 0 0 0-5 5c0 3.5 5 8 5 8s5-4.5 5-8a5 5 0 0 0-5-5zm0 7a2 2 0 1 1 0-4 2 2 0 0 1 0 4z" fill="#cfcfcf"/></svg><span>14 Rue Valmont 75011 Lyonnais,<br>France</span></div>
    <div class="office-row"><svg width="11" height="11" viewBox="0 0 11 11"><rect width="11" height="11" rx="2" fill="#cfcfcf"/><path d="M3 2.5l1.5 1.2-.8 1.2a5 5 0 0 0 2.4 2.4l1.2-.8L8.5 8 7.6 9C5 8.6 2.4 6 2 3.4z" fill="#262626"/></svg><span>01 23 60 71 40<br>01 23 60 71 42</span></div>
    <div class="office-row"><svg width="12" height="9" viewBox="0 0 12 9"><rect x=".5" y=".5" width="11" height="8" fill="none" stroke="#cfcfcf"/><path d="M.5.5 6 5l5.5-4.5" fill="none" stroke="#cfcfcf"/></svg><span>info@tevlora.com</span></div>
  </div>
  <div class="fcol" style="left:765px;width:240px">
    <h4>LATEST TWEETS</h4>
    <p class="tweet">Site Template | Theme Library | Creative Website | Bravick Studio <a href="#">http://lnk.example/a41c</a><small>about 3 hours ago</small></p>
    <p class="tweet">Orsel II <a href="#">http://lnk.example/b73d</a><small>about 1 day ago</small></p>
  </div>
</footer>

<div class="abs base">
  <p>© 2014 Tevlora All Rights Reserved</p>
  <span class="social" style="left:895px" aria-label="Social profile"></span>
  <span class="social" style="left:932px" aria-label="Social profile"></span>
  <span class="social" style="left:968px" aria-label="Social profile"></span>
</div>

</body>
</html>
```